SOLVE Study flyer

I need help designing a flyer for a research study that will include brain imaging in adolescents. The info is in the attached document. The study is called the Sequoia Outlook Lantern Valley Echo (SOLVE) study. Ideally this would be returned as a document that I can edit in the future as we will have several new recruitment phases (different age groups, etc. I also would love to have a logo designed as part of this project, but I recognize that might be a separate design request.

```html
<!DOCTYPE html>
<html lang="en">
<head>
<meta charset="utf-8">
<title>SOLVE Study Flyer</title>
<link href="https://fonts.googleapis.com/css2?family=Saira+Condensed:ital,wght@0,700;0,800;0,900;1,800&family=Outfit:wght@400;500&display=swap" rel="stylesheet">
<style>
  :root {
    --teal: #008274;
    --ink: #111111;
    --paper: #ffffff;
    --backdrop: #c8c8c8;
    --photo-light: #e8eef3;
    --photo-blue: #7fa9c6;
    --photo-deep: #2f5d7e;
    --photo-warm: #c9a27f;
  }
  * { box-sizing: border-box; margin: 0; padding: 0; }
  html, body { width: 906px; height: 1200px; overflow: hidden; background: var(--backdrop); }
  .flyer {
    position: absolute; left: 53px; top: 0; width: 800px; height: 1200px;
    background: var(--paper); overflow: hidden;
    font-family: "Outfit", sans-serif;
  }
  .display { font-family: "Saira Condensed", sans-serif; text-transform: uppercase; }

  .hero { position: absolute; left: 0; top: 0; width: 800px; height: 403px; }
  .hero-photo {
    position: absolute; left: 300px; top: 0; width: 500px; height: 403px;
    background:
      linear-gradient(90deg, var(--paper) 0%, rgba(255,255,255,0.6) 22%, rgba(255,255,255,0) 45%),
      linear-gradient(90deg, var(--photo-light) 0%, var(--photo-blue) 40%, var(--photo-deep) 58%, var(--photo-warm) 72%, var(--photo-light) 86%, var(--photo-blue) 100%);
  }
  .study-name {
    position: absolute; left: 11px; top: 22px; width: 480px;
    color: var(--teal); font-weight: 800; font-size: 27px; line-height: 29px; letter-spacing: 0.3px;
  }
  .headline {
    position: absolute; left: 12px; top: 92px; width: 460px;
    color: var(--ink); font-weight: 900; font-size: 47px; line-height: 43px;
  }
  .intro {
    position: absolute; left: 12px; top: 317px; width: 470px;
    color: var(--ink); font-size: 14.3px; line-height: 21px;
  }

  .involves {
    position: absolute; left: 0; top: 403px; width: 800px; height: 326px;
    background: var(--teal); color: var(--paper);
  }
  .involves h2 {
    text-align: center; font-weight: 800; font-size: 27px; margin-top: 29px; letter-spacing: 0.4px;
  }
  .involves ul { list-style: none; margin: 27px 0 0 118px; width: 620px; }
  .involves li { position: relative; font-size: 21.5px; line-height: 26.5px; margin-bottom: 22px; }
  .involves li::before {
    content: ""; position: absolute; left: -28px; top: 8px; width: 11px; height: 11px;
    border-radius: 50%; background: var(--paper);
  }

  .eligible {
    position: absolute; left: 47px; top: 754px; width: 707px; height: 269px;
    border: 2px solid var(--teal); border-radius: 28px;
  }
  .eligible-tab {
    position: absolute; left: 136px; top: 740px; width: 527px; height: 53px;
    background: var(--teal); color: var(--paper); border-radius: 6px;
    font-weight: 800; font-size: 27px; letter-spacing: 0.4px;
    display: flex; align-items: center; justify-content: center;
  }
  .criterion { position: absolute; top: 817px; width: 220px; text-align: center; }
  .criterion-icon {
    width: 113px; height: 113px; border-radius: 50%; background: var(--teal);
    margin: 0 auto; display: flex; align-items: center; justify-content: center;
  }
  .criterion p { font-size: 17px; line-height: 21px; color: var(--ink); margin-top: 22px; }

  .contact {
    position: absolute; left: 0; top: 1047px; width: 800px; height: 153px;
    background: var(--teal); color: var(--paper);
  }
  .contact-call {
    text-align: center; font-weight: 800; font-style: italic; font-size: 26px; line-height: 30px;
    margin-top: 13px; letter-spacing: 0.4px;
  }
  .email {
    position: absolute; left: 76px; top: 98px; display: flex; align-items: center; gap: 12px;
    font-size: 24px;
  }
  .email-dot {
    width: 37px; height: 37px; border-radius: 50%; background: var(--paper);
    display: flex; align-items: center; justify-content: center;
  }
  .compensation {
    position: absolute; left: 504px; top: 82px; width: 296px; height: 71px;
    background: var(--paper); border-top-left-radius: 22px; color: var(--teal);
    text-align: center; font-weight: 800; font-size: 30px; line-height: 30px; padding-top: 7px;
    letter-spacing: 0.5px;
  }
</style>
</head>
<body>
  <main class="flyer">
    <section class="hero">
      <div class="hero-photo" role="img" aria-label="Photo of a researcher fitting an EEG sensor cap on a young woman, with a brain scan display in the background"></div>
      <p class="study-name display">Sequoia Outlook Lantern<br>Valley Echo</p>
      <h1 class="headline display">Are you the parent of a child age 10-17? Do they worry or overthink negative emotions?</h1>
      <p class="intro">Northvale University researchers are seeking girls age 10-17 for a study about brain activity in emotions and decision-making and how they relate to puberty, anxiety and depression.</p>
    </section>

    <section class="involves">
      <h2 class="display">Study participation involves</h2>
      <ul>
        <li>One one-hour interview (online or in-person) where your child will discuss their thoughts</li>
        <li>Online questionnaires (parent and child)</li>
        <li>One two-hour visit where your child will complete an MRI scan, answer questions about their puberty stage, and have a small hair sample taken to study puberty hormones</li>
      </ul>
    </section>

    <div class="eligible"></div>
    <div class="eligible-tab display">Your child may be eligible if they</div>

    <div class="criterion" style="left:20px;">
      <div class="criterion-icon">
        <svg width="64" height="64" viewBox="0 0 64 64" fill="none" stroke="#fff" stroke-width="2.5">
          <path d="M50 20 A24 24 0 1 0 54 38" stroke-dasharray="3 2"/>
          <path d="M52 26 v14 m-5 -5 l5 6 l5 -6"/>
          <text x="30" y="37" fill="#fff" stroke="none" font-family="Outfit, sans-serif" font-size="14" font-weight="500" text-anchor="middle">AGE</text>
        </svg>
      </div>
      <p>Are age 10-17</p>
    </div>

    <div class="criterion" style="left:244px;">
      <div class="criterion-icon">
        <svg width="64" height="64" viewBox="0 0 64 64" fill="none" stroke="#fff" stroke-width="2.2" stroke-linecap="round">
          <ellipse cx="26" cy="20" rx="18" ry="11"/>
          <text x="26" y="25" fill="#fff" stroke="none" font-family="Outfit, sans-serif" font-size="13" font-weight="500" text-anchor="middle">???</text>
          <path d="M34 32 c10 0 16 6 16 14 l4 6 h-4 v6 h-8 v4"/>
        </svg>
      </div>
      <p>Tend to worry or overthink negative thoughts</p>
    </div>

    <div class="criterion" style="left:512px;">
      <div class="criterion-icon">
        <svg width="64" height="64" viewBox="0 0 64 64" fill="none" stroke="#fff" stroke-width="2">
          <rect x="38" y="8" width="12" height="12" rx="2"/>
          <rect x="26" y="14" width="9" height="9" rx="2"/>
          <rect x="10" y="26" width="9" height="9" rx="2"/>
          <rect x="12" y="44" width="9" height="9" rx="2"/>
          <rect x="48" y="26" width="9" height="9" rx="2"/>
          <circle cx="34" cy="38" r="9"/>
          <path d="M22 58 c2 -8 22 -8 24 0"/>
        </svg>
      </div>
      <p>Have not been diagnosed with psychosis, learning problems, or autism</p>
    </div>

    <section class="contact">
      <p class="contact-call display">Interested in participating?<br>Want more information? Please contact us!</p>
      <div class="email">
        <span class="email-dot">
          <svg width="20" height="14" viewBox="0 0 20 14" fill="none" stroke="#008274" stroke-width="1.6">
            <rect x="1" y="1" width="18" height="12"/>
            <path d="M1 1 l9 7 l9 -7"/>
          </svg>
        </span>
        <span>solvestudy@northvale-health.edu</span>
      </div>
      <div class="compensation display">Compensation<br>up to $140</div>
    </section>
  </main>
</body>
</html>
```